Custom Proposal

We need a custom proposal template created for our company. Our company, BRIGHTWAVE AUDIO SERVICES, provides in-store music and messaging services to businesses in the US and Canada. We need a 3-4 page document created that outlines our products and services that will accompany their proposal. The proposal needs to be created using company colors with a fresh feeling. Our music service is top quality and we service many major brands with customized music service. We have all of the copy and logos for partner companies. We need a designer to create a layout that will express our products and services in a fresh and exciting way.

Attached to this project you will find the following:

- PDF file title "Example". This is an example file of what we are looking for (minus the last page with the order fields).

- BRIGHTWAVE AUDIO SERVICES logo in EPS

- BRIGHTWAVE AUDIO SERVICES brand standards guideline

- Text copy for the flyer

- Styles (these match our web site)

- Font used on our web site and other material

- Zip file with logos of companies we do business with

We would also like a section that has the logos for these companies to showcase who we work with.

We prefer to have the project developed in an editable format such as Adobe Illustrator or PSD.

The paper size is 8 1/2" x 11" Portrait
Updates

Please note: We do NOT want the graphics included in the "Brands Standard Guide" that is attached to the project to be used for the project. The Brand Standards Guide is provided simply to show you how to use our logo, not to include the graphics used in the guide. Also, we do not want any computers or smart phones in the artwork. We provided the Pellow Harbor document as an example of one we liked, not to use the same graphics.

Please be sure to follow the outline of the project and use the images  supplied. Please also keep in mind we  are not looking for a template look  but rather  a  unique design  for each page that is themed for our industry. Our industry is in-store music and messaging services.

Thank you

Target Market(s)

Business owners, executives, marketing directors, business executives

Industry/Entity Type

Business

Requirements
Must have
• We are looking for fresh, open, personal, exciting, creative, and relevant designs.
Should not have
• We are NOT looking for stock template looking designs with no originality that look like a standard stock design.

```html
<!DOCTYPE html>
<html lang="en">
<head>
<meta charset="utf-8">
<title>Brightwave Audio Services – Services</title>
<link href="https://fonts.googleapis.com/css2?family=Open+Sans:wght@300;400;700&display=swap" rel="stylesheet">
<style>
:root{
  --green:#8dc63f;
  --green-dark:#6e9f22;
  --bar:#4a4b4d;
  --text:#4d4d4f;
  --night:#05070d;
  --paper:#ffffff;
  --paper-low:#dcdde0;
}
*{margin:0;padding:0;box-sizing:border-box}
html,body{width:848px;height:1200px;overflow:hidden}
body{font-family:"Open Sans",Arial,sans-serif;color:var(--text);
  background:linear-gradient(to bottom,var(--paper) 0%,var(--paper) 60%,var(--paper-low) 100%);position:relative}
.masthead{position:absolute;left:0;top:46px;width:848px;height:117px;background:var(--night)}
.masthead-brand{position:absolute;left:0;top:0;height:117px;width:420px;
  background:linear-gradient(100deg,var(--green-dark),var(--green));
  clip-path:polygon(0 0,100% 0,86% 100%,0 100%)}
.masthead-sound{position:absolute;left:380px;top:0;width:468px;height:117px;
  background:radial-gradient(ellipse 60% 30% at 55% 50%,#3fa6e8 0%,#0e3a6a 45%,var(--night) 80%)}
.brand-mark{position:absolute;left:30px;top:44px;width:28px;height:28px;background:var(--paper)}
.brand-name{position:absolute;left:72px;top:34px;color:var(--paper);font-weight:400;font-size:24px;line-height:1.15;letter-spacing:.3px}
.section-bar{position:absolute;left:0;height:44px;background:var(--bar);color:var(--paper);
  font-weight:700;font-size:26px;line-height:44px;padding-left:30px;
  clip-path:polygon(0 0,100% 0,calc(100% - 40px) 100%,0 100%)}
.subhead{position:absolute;left:30px;width:480px;color:var(--green-dark);font-weight:700;font-size:15px;line-height:1.15;text-transform:uppercase}
.copy{position:absolute;left:30px;width:482px;font-weight:300;font-size:13.6px;line-height:1.28;text-align:justify}
.copy ul{list-style:none}
.copy li::before{content:"";display:inline-block;width:5px;height:5px;background:var(--green);margin:0 6px 2px 0}
.photo{position:absolute;left:536px;width:312px}
</style>
</head>
<body>
<header class="masthead">
  <div class="masthead-sound" role="img" aria-label="Blue glowing audio waveform on a dark background"></div>
  <div class="masthead-brand">
    <div class="brand-mark"></div>
    <div class="brand-name">Brightwave Audio Services</div>
  </div>
</header>

<h2 class="section-bar" style="top:204px;width:318px">SERVICES</h2>
<h3 class="subhead" style="top:260px">Full service in-store music solutions.</h3>
<p class="copy" style="top:278px">INSTALLATION BRIGHTWAVE AUDIO SERVICES™ offers a wide array of services to meet a variety of needs for a range of business sizes and budgets. Our goal is simple, pinpoint and deploy optimal messaging for your brand and boost your business by creating a truly unique experience for you</p>
<h3 class="subhead" style="top:378px">We do everything.</h3>
<p class="copy" style="top:396px">Trust our professionals to handle your installation and servicing. With over 8,000 trained, licensed and insured technicians and installers at your disposal, nationwide, we've covered every zip code in the country. We'll even train your staff on the proper use of your new equipment when we complete your installation.</p>

<h2 class="section-bar" style="top:524px;width:438px">SERVICE LEVEL AGREEMENT</h2>
<h3 class="subhead" style="top:572px">SLA's</h3>
<div class="copy" style="top:590px"><p>Warranty your investment and ensure the least amount of downtime with our Service Level Agreements, complete with customized warranty and service solutions, tailored to meet your needs.</p>
<ul><li>Damaged or Defective Equipment Replacement</li><li>On-site Service Assistance by a Trained Technician</li></ul></div>

<h2 class="section-bar" style="top:714px;width:438px">CUSTOM SOLUTIONS</h2>
<h3 class="subhead" style="top:770px">We all have different needs.</h3>
<p class="copy" style="top:790px">BRIGHTWAVE AUDIO SERVICES™ provides our customers and yours with streaming music services and fully customized streaming radio on a network developed specifically for your business. Each hour consists of a great mix of music and optimal messaging, selected and tailored to amplify your brand in the best way possible. All music is streamed via Internet connection utilizing a digital media player that we install for you.</p>

<h2 class="section-bar" style="top:941px;width:438px">FRANCHISE SOLUTIONS</h2>
<h3 class="subhead" style="top:996px">Affordable, standardized &amp; hassle-free to<br>meet your needs.</h3>
<p class="copy" style="top:1034px">We know that franchises and chain stores are looking for the most straightforward solution in a digital media and messaging service. That's why we offer easy-to-use, accessible, quality audio and messaging services. Cover one, a few or all franchise locations with confidence and enjoy exclusive benefits.</p>

<svg class="photo" style="top:208px" width="312" height="220" viewBox="0 0 312 220" role="img" aria-label="Photo of smiling staff in aprons at a shop counter">
  <defs><linearGradient id="p1" x1="0" y1="0" x2="1" y2="1"><stop offset="0" stop-color="#e9a14a"/><stop offset="1" stop-color="#6b3f24"/></linearGradient></defs>
  <polygon points="6,0 22,0 42,220 26,220" fill="var(--green)"/>
  <polygon points="22,0 312,0 312,220 42,220" fill="url(#p1)"/>
</svg>
<svg class="photo" style="top:468px" width="312" height="222" viewBox="0 0 312 222" role="img" aria-label="Photo of a business team looking at a tablet together">
  <defs><linearGradient id="p2" x1="0" y1="0" x2="1" y2="1"><stop offset="0" stop-color="#d9dde0"/><stop offset="1" stop-color="#4b5560"/></linearGradient></defs>
  <polygon points="6,0 22,0 42,222 26,222" fill="var(--green)"/>
  <polygon points="22,0 312,0 312,222 42,222" fill="url(#p2)"/>
</svg>
<svg class="photo" style="top:718px" width="312" height="218" viewBox="0 0 312 218" role="img" aria-label="Photo of a woman enjoying music on headphones">
  <defs><linearGradient id="p3" x1="0" y1="0" x2="1" y2="1"><stop offset="0" stop-color="#f3e4d2"/><stop offset="1" stop-color="#b85a48"/></linearGradient></defs>
  <polygon points="6,0 22,0 42,218 26,218" fill="var(--green)"/>
  <polygon points="22,0 312,0 312,218 42,218" fill="url(#p3)"/>
</svg>
<svg class="photo" style="top:966px" width="312" height="234" viewBox="0 0 312 234" role="img" aria-label="Photo of friends laughing over a meal at a restaurant">
  <defs><linearGradient id="p4" x1="0" y1="0" x2="1" y2="1"><stop offset="0" stop-color="#c9a27a"/><stop offset="1" stop-color="#4a2c1c"/></linearGradient></defs>
  <polygon points="6,0 22,0 42,234 26,234" fill="var(--green)"/>
  <polygon points="22,0 312,0 312,234 42,234" fill="url(#p4)"/>
</svg>
</body>
</html>
```